Property Developer Business card design

we need a business card design + printing for a new Property developer company based in melbourne.
We are a group of investors investing in a property developer business. We have more projects involved in residential property as opposed to commercial property but we are involved in both market. we also provide consulting services with overseas investors willing to invest in the australian property market.
Updates
I have uploaded the logo. I'm not very convince with the colors of my logo... any suggestion please?.
Thanks guys!
Target Market(s)
property investors or person willing to purchase investment property
Industry/Entity Type
Residential
Contact Information for Business Card
Bramblecourt Holdings Australia Pty Ltd
Look and feel

```html
<!DOCTYPE html>
<html lang="en">
<head>
<meta charset="utf-8">
<title>Bramblecourt Holdings Australia – Business Card</title>
<link rel="stylesheet" href="https://fonts.googleapis.com/css2?family=Questrial&display=swap">
<style>
  :root {
    --page-bg: #e9e7e4;
    --card-black: #141414;
    --brand-blue: #0a8ef0;
    --white: #ffffff;
    --icon-dark: #1c1c1c;
    --card-w: 740px;
    --card-h: 430px;
  }
  * { box-sizing: border-box; margin: 0; padding: 0; }
  html, body {
    width: 1200px;
    height: 1000px;
    overflow: hidden;
    background: var(--page-bg);
    font-family: "Questrial", "Century Gothic", sans-serif;
  }
  .sheet {
    width: 1200px;
    height: 1000px;
    display: flex;
    flex-direction: column;
    align-items: center;
    justify-content: center;
    gap: 50px;
  }
  .card {
    position: relative;
    width: var(--card-w);
    height: var(--card-h);
    background: var(--card-black);
    border-radius: 44px 0 44px 0;
    overflow: hidden;
    box-shadow: 0 6px 18px rgba(0,0,0,0.18);
  }
  .card-swoosh {
    position: absolute;
    inset: 0;
    width: 100%;
    height: 100%;
  }
  .brand {
    position: absolute;
    display: flex;
    align-items: center;
    color: var(--brand-blue);
    white-space: nowrap;
  }
  .brand-mark {
    background: var(--white);
    flex: none;
  }
  .card-front .brand {
    left: 48px;
    top: 78px;
    font-size: 31px;
    gap: 14px;
  }
  .card-front .brand-mark { width: 28px; height: 28px; }

  .holder {
    position: absolute;
    left: 0;
    top: 292px;
  }
  .holder-name {
    display: inline-block;
    background: var(--brand-blue);
    color: var(--white);
    font-size: 22px;
    letter-spacing: 1px;
    padding: 4px 16px 5px 14px;
  }
  .holder-role {
    color: var(--white);
    font-size: 11px;
    letter-spacing: 0.5px;
    margin: 6px 0 0 44px;
  }

  .contacts {
    position: absolute;
    right: 20px;
    top: 330px;
    list-style: none;
    text-align: right;
    color: var(--white);
    font-size: 12.5px;
    letter-spacing: 1.6px;
    line-height: 18px;
  }
  .contacts li {
    display: flex;
    justify-content: flex-end;
    align-items: center;
    gap: 6px;
  }
  .contacts svg { width: 12px; height: 12px; flex: none; }

  .card-back .brand {
    left: 0;
    right: 0;
    justify-content: center;
    top: 192px;
    font-size: 36px;
    gap: 18px;
  }
  .card-back .brand-mark { width: 40px; height: 40px; }
</style>
</head>
<body>
<main class="sheet">

  <section class="card card-front" aria-label="Business card front">
    <svg class="card-swoosh" viewBox="0 0 740 430" preserveAspectRatio="none" aria-hidden="true">
      <path d="M0,430 C300,385 650,240 740,40 L740,110 C640,300 360,400 0,430 Z" fill="#ffffff"/>
      <path d="M0,430 C360,400 640,300 740,110 L740,430 Z" fill="#0a8ef0"/>
    </svg>

    <div class="brand">
      <span class="brand-mark"></span>
      <span class="brand-name">Bramblecourt Holdings Australia</span>
    </div>

    <div class="holder">
      <div class="holder-name">Dana Whitfield</div>
      <div class="holder-role">Managing Director</div>
    </div>

    <ul class="contacts">
      <li>0400 582 316
        <svg viewBox="0 0 13 13" aria-hidden="true"><rect x="3.5" y="0.5" width="6" height="12" rx="1" fill="none" stroke="#1c1c1c" stroke-width="1.2"/></svg>
      </li>
      <li>+61 3 9012 4470
        <svg viewBox="0 0 13 13" aria-hidden="true"><path d="M3,1 L5,1 L6,4 L4.5,5.2 C5.3,7 6.2,8 8,8.6 L9,7 L12,8 L12,10.5 C8,12 2,7 3,1 Z" fill="#1c1c1c"/></svg>
      </li>
      <li>dana.whitfield@bramblecourt.com.au
        <svg viewBox="0 0 13 13" aria-hidden="true"><rect x="0.5" y="2.5" width="12" height="8" fill="#1c1c1c"/><path d="M0.5,2.5 L6.5,7 L12.5,2.5" fill="none" stroke="#0a8ef0" stroke-width="1"/></svg>
      </li>
      <li>www.bramblecourtholdings.com
        <svg viewBox="0 0 13 13" aria-hidden="true"><rect x="3" y="0.5" width="7" height="12" rx="3.5" fill="#1c1c1c"/><line x1="6.5" y1="2" x2="6.5" y2="5" stroke="#0a8ef0" stroke-width="1"/></svg>
      </li>
    </ul>
  </section>

  <section class="card card-back" aria-label="Business card back">
    <div class="brand">
      <span class="brand-mark"></span>
      <span class="brand-name">Bramblecourt Holdings Australia</span>
    </div>
  </section>

</main>
</body>
</html>
```